business card for a massage therapy practice named 'Cedar and Willow Massage Studio'

I really need a trendy, yet easy on the eyes business card to complement my logo. Ideally with some gold or rose gold foil work.

My uploaded file of the logo I have in horizontal but I have a vertical version as well. Another color that is used in the website is a blush pink here and there. I'd like to see some trendy tropical leaves in the design.

```html
<!DOCTYPE html>
<html lang="en">
<head>
<meta charset="utf-8">
<title>Cedar and Willow Massage Studio – Business Card</title>
<link href="https://fonts.googleapis.com/css2?family=Work+Sans:wght@400;500&family=Kaushan+Script&display=swap" rel="stylesheet">
<style>
  :root {
    --backdrop: #2b2a29;
    --gold-light: #ab9869;
    --gold: #9a8558;
    --gold-dark: #8c784d;
    --paper: #ffffff;
    --ink: #1e1e1e;
    --mint: #7fd3c1;
  }
  * { box-sizing: border-box; margin: 0; padding: 0; }
  html, body {
    width: 1200px; height: 930px; overflow: hidden;
    background: var(--backdrop);
    font-family: "Work Sans", Arial, sans-serif;
  }
  .canvas { position: relative; width: 1200px; height: 930px; }

  .card {
    position: absolute;
    width: 700px; height: 400px;
    border-radius: 22px;
    box-shadow: 0 18px 40px rgba(0,0,0,0.45);
  }

  /* Front: gold foil side */
  .card-front {
    left: 120px; top: 50px;
    background: linear-gradient(125deg, var(--gold-light) 0%, var(--gold) 55%, var(--gold-dark) 100%);
    display: flex; align-items: center; justify-content: center;
  }
  .brand {
    display: flex; align-items: center; gap: 18px;
  }
  .brand-dot {
    width: 46px; height: 46px; border-radius: 50%;
  }
  .brand-name {
    font-weight: 500; letter-spacing: 0.04em;
  }
  .card-front .brand-dot { background: var(--paper); }
  .card-front .brand-name { color: var(--paper); font-size: 30px; line-height: 1.2; }

  /* Back: details side */
  .card-back {
    left: 380px; top: 480px;
    background: var(--paper);
  }
  .card-back .brand {
    position: absolute; left: 48px; top: 78px;
  }
  .card-back .brand-dot { background: var(--gold); width: 36px; height: 36px; }
  .card-back .brand-name { color: var(--ink); font-size: 21px; line-height: 1.25; }

  .holder-name {
    position: absolute; right: 56px; top: 138px;
    font-family: "Kaushan Script", cursive;
    font-size: 44px; color: var(--gold);
    word-spacing: 10px;
  }
  .divider {
    position: absolute; left: 48px; right: 40px; top: 214px;
    height: 2px; background: var(--gold);
  }
  .address {
    position: absolute; right: 56px; top: 238px;
    font-size: 17px; line-height: 1.35; color: var(--ink); text-align: left;
  }
  .contacts {
    position: absolute; left: 48px; top: 250px;
    list-style: none;
    font-size: 19px; line-height: 1; color: var(--ink);
  }
  .contacts li { display: flex; align-items: center; gap: 12px; margin-bottom: 11px; }
  .contacts svg { width: 14px; height: 14px; flex: none; }
  .contacts .accent { color: var(--gold); }
</style>
</head>
<body>
<main class="canvas">

  <section class="card card-front" aria-label="Card front">
    <div class="brand">
      <span class="brand-dot"></span>
      <span class="brand-name">Cedar and Willow<br>Massage Studio</span>
    </div>
  </section>

  <section class="card card-back" aria-label="Card back">
    <div class="brand">
      <span class="brand-dot"></span>
      <span class="brand-name">Cedar and Willow<br>Massage Studio</span>
    </div>

    <p class="holder-name">Marisol Vega</p>
    <div class="divider"></div>

    <p class="address">2417 Alder St. suite 210,<br>Sacramento, CA 95816</p>

    <ul class="contacts">
      <li>
        <svg viewBox="0 0 16 16" aria-hidden="true"><path d="M4 1.5l2.5 3-1.4 1.6a9 9 0 0 0 4.8 4.8L11.5 9.5l3 2.5-1.6 2.4C7 14 2 9 1.6 3.1z" fill="#9a8558"/></svg>
        (916) 555-0148
      </li>
      <li>
        <svg viewBox="0 0 16 16" aria-hidden="true"><rect x="1.5" y="3.5" width="13" height="9" fill="none" stroke="#9a8558" stroke-width="1.5"/><path d="M1.5 3.5L8 9l6.5-5.5" fill="none" stroke="#9a8558" stroke-width="1.5"/></svg>
        cedarandwillow@gmail.com
      </li>
      <li>
        <svg viewBox="0 0 16 16" aria-hidden="true"><circle cx="8" cy="8" r="6.5" fill="none" stroke="#9a8558" stroke-width="1.4"/><ellipse cx="8" cy="8" rx="2.8" ry="6.5" fill="none" stroke="#9a8558" stroke-width="1.2"/><path d="M1.5 8h13" stroke="#9a8558" stroke-width="1.2"/></svg>
        <span>www.<span class="accent">cedarandwillow</span>.com</span>
      </li>
    </ul>
  </section>

</main>
</body>
</html>
```